For Lease Sign to Attract National Retail Tenants

Attached is a logo design that was created by Pixel Harbor. I will like to develop a leasing sign that is 4 foot wide by 4 foot high or 4 feet wide and 6 feet high. I would like the sign to have a black background and use the colors that are in the logo. These will be signs that are placed in front of shopping centers and are often read by passing motorist so the sign must be simple, clean, very easy to read, distinctive, and have as few words as possible. It would be good if small amounts of bright green can be added as a boarder or ????? The text should be FOR LEASE, 415-738-2916, Rod Kellaway. I will want to also design cards and letter head around the same theme.

Target Market(s)

National retail tenants wanting to lease space in my shopping centers

Industry/Entity Type

Real Estate Development

Contact Information for Business Card

Tall Oak Holdings, LLC Rod Kellaway President & CEO 4127 Marlow Ave. Suite 308 La Jolla, CA 92037 415-738-2916 rodkellaway@quillpost.net

```html
<!DOCTYPE html>
<html lang="en">
<head>
<meta charset="utf-8">
<title>For Lease Sign – Tall Oak Holdings</title>
<link href="https://fonts.googleapis.com/css2?family=Montserrat:wght@500;600;800&display=swap" rel="stylesheet">
<style>
  :root {
    --sign-red: #ee4144;
    --phone-red: #e8262c;
    --frame-grey: #9b9b9b;
    --ink: #3f3a3a;
    --paper: #ffffff;
  }
  html, body {
    margin: 0;
    padding: 0;
    width: 1200px;
    height: 1200px;
    overflow: hidden;
    background: var(--paper);
  }
  .canvas {
    position: relative;
    width: 1200px;
    height: 1200px;
    font-family: "Montserrat", sans-serif;
  }
  .sign-shapes {
    position: absolute;
    inset: 0;
    width: 1200px;
    height: 1200px;
  }
  .headline,
  .company-name,
  .phone,
  .agent-name {
    position: absolute;
    left: 0;
    width: 1204px;
    margin: 0;
    text-align: center;
    line-height: 1;
    white-space: nowrap;
  }
  .headline {
    color: var(--paper);
    font-weight: 800;
    font-size: 117px;
    letter-spacing: 0;
  }
  .headline--for { top: 389px; left: -12px; }
  .headline--lease { top: 475px; left: 8px; }
  .company-name {
    top: 768px;
    font-weight: 600;
    font-size: 25px;
    color: var(--phone-red);
    letter-spacing: 0.5px;
  }
  .phone {
    top: 846px;
    font-weight: 500;
    font-size: 51px;
    color: var(--phone-red);
  }
  .agent-name {
    top: 904px;
    font-weight: 500;
    font-size: 40px;
    color: var(--ink);
  }
</style>
</head>
<body>
<main class="canvas">
  <svg class="sign-shapes" viewBox="0 0 1500 1500" aria-hidden="true">
    <rect class="sign-frame" x="414" y="237" width="677" height="1027" fill="var(--paper)" stroke="var(--frame-grey)" stroke-width="18"/>
    <polygon class="chevron-stripe" points="408,280 750,372 1090,282 1090,336 750,427 408,336" fill="var(--sign-red)"/>
    <polygon class="chevron-banner" points="408,380 750,472 1090,380 1090,730 750,821 408,730" fill="var(--sign-red)"/>
  </svg>

  <h1 class="headline headline--for">FOR</h1>
  <p class="headline headline--lease">LEASE</p>

  <p class="company-name">Tall Oak Holdings, LLC</p>
  <p class="phone">415-738-2916</p>
  <p class="agent-name">Rod Kellaway</p>
</main>
</body>
</html>
```